Business Identity Stationary

Already have the logo which is in the attached files so only need the Business STationary
1) Double Sided Business Card
2) Letterhead
3) Presentation folder with business card holder on inside cover
4) WIth compliments slip
See information for business cards, letterhead and presentation folder below.

This should be a simply job using a logo we already had designed along with a little device. I suggest using the device off center and perhaps lower in the corner in an abstract way. Also the logo device could be used as a watermark for the letterhead. The designer who created the logo presented something that I think works well for a business card. The front of the double sided business card could have the name logo small for the website address and only use the Lime device on the front. Then on the back could be the name Barrow Advisory logo.

Please note that for the business card the black and lime green background do look good. Also please think of using the lime device separately in an unusual way.

It has been brought to my attention that.my budget was far to low. Hopefully this.will attract you to the project. 

The parent company of Barrow Advisory is TallHeron holdings. I have uploaded a file of the Tall Heron business card I really like. Perhaps use this business card as a guide to the type of modern and clean style I am looking for. It also works to have the Barrow Advisroy and Tall Heron similar.

Reason: Still haven't received anything exactly right.

Industry/Entity Type

Business

Font styles to use
Sans Serif

Colors
9bcb3c
000000
5c5c5c
add136
cadf82
eaf2cf
f9fbf2
1b1b1b
757575

Requirements
Must have
• 1) Double Sided Business Card
Marta Kellendorf
Director
Tel: +505 8264 3170
Email: mk@barrowadvisory-example.com
Website: www.barrowadvisory-example.com

Frederick Kellendorf
Director
Tel: +505 8264 3172
Email: fk@barrowadvisory-example.com

Lucia Brenes Otaduy
Director
Tel: 8642 1093
Email: lbo@barrowadvisory-example.com

2) Letterhead
Logo
Lime Logo Device
Website Address: www.barrowadvisory-example.com
Small print on bottom: Barrow Advisory a Tall Heron Holding Company SA. RUC J0487000239518

3) Presentation Folder
Traditional Presentation folder with inside front cover spot for the insertion of business card.

4) With Compliments slip

```html
<!DOCTYPE html>
<html lang="en">
<head>
<meta charset="utf-8">
<title>Barrow Advisory – Business Card</title>
<link rel="stylesheet" href="https://fonts.googleapis.com/css2?family=Raleway:wght@300;400;600&display=swap">
<style>
  :root{
    --lime:#9bcb3c;
    --black:#000000;
    --ink:#1b1b1b;
    --grey:#5c5c5c;
    --white:#ffffff;
    --canvas:#ecece8;
  }
  *{box-sizing:border-box;margin:0;padding:0}
  html,body{width:1200px;height:1024px;overflow:hidden}
  body{background:var(--canvas);font-family:"Raleway",Arial,sans-serif;position:relative}

  .card{position:absolute;width:600px;height:343px;overflow:hidden;box-shadow:0 6px 18px rgba(0,0,0,.18)}

  /* Front card */
  .card--front{left:60px;top:100px;background:var(--white)}
  .card__band{position:absolute;left:0;right:0;bottom:0;height:158px;background:var(--ink)}
  .wordmark{position:absolute;display:flex;align-items:center;gap:14px;font-weight:300;letter-spacing:.02em;white-space:nowrap}
  .wordmark__dot{display:block;border-radius:50%;background:var(--lime)}
  .card--front .wordmark{left:42px;top:92px;font-size:40px;color:var(--black)}
  .card--front .wordmark__dot{width:22px;height:22px}

  .contact{position:absolute;left:42px;top:208px;color:var(--white);font-size:13px;line-height:22px}
  .contact__name{font-size:17px;font-weight:600;color:var(--lime);margin-bottom:6px}
  .contact__role{font-weight:400;color:var(--white)}
  .contact__row{display:flex;align-items:center;gap:9px}
  .contact__row svg{flex:none}

  /* Back card */
  .card--back{left:540px;top:580px;background:var(--ink)}
  .card--back .wordmark{left:0;right:0;top:110px;justify-content:center;font-size:50px;color:var(--white)}
  .card--back .wordmark__dot{width:26px;height:26px}
  .card__rule{position:absolute;left:0;top:282px;width:238px;height:2px;background:var(--lime)}
  .card__web{position:absolute;left:252px;top:273px;font-size:15px;color:var(--white);letter-spacing:.01em}
  .card__web em{font-style:normal;color:var(--lime)}
</style>
</head>
<body>

<section class="card card--front" aria-label="Business card front">
  <div class="card__band"></div>
  <div class="wordmark"><span>Barrow Advisory</span><span class="wordmark__dot"></span></div>
  <div class="contact">
    <p class="contact__name">Marta Kellendorf <span class="contact__role">| Director</span></p>
    <p class="contact__row">
      <svg width="11" height="11" viewBox="0 0 24 24" aria-hidden="true"><path fill="var(--lime)" d="M6.6 10.8a15 15 0 0 0 6.6 6.6l2.2-2.2c.3-.3.7-.4 1-.2 1.1.4 2.3.6 3.6.6.6 0 1 .4 1 1V20c0 .6-.4 1-1 1A17 17 0 0 1 3 4c0-.6.4-1 1-1h3.5c.6 0 1 .4 1 1 0 1.3.2 2.5.6 3.6.1.3 0 .7-.2 1z"/></svg>
      +505 8264 3170</p>
    <p class="contact__row">
      <svg width="11" height="11" viewBox="0 0 24 24" aria-hidden="true"><rect x="2" y="5" width="20" height="14" fill="var(--lime)"/><path d="M2 5l10 8 10-8" fill="none" stroke="var(--ink)" stroke-width="2"/></svg>
      mk@barrowadvisory-example.com</p>
    <p class="contact__row">
      <svg width="11" height="11" viewBox="0 0 24 24" aria-hidden="true"><circle cx="12" cy="12" r="10" fill="var(--lime)"/><path d="M2 12h20M12 2c3 3 3 17 0 20M12 2c-3 3-3 17 0 20" fill="none" stroke="var(--ink)" stroke-width="1.6"/></svg>
      www.barrowadvisory-example.com</p>
  </div>
</section>

<section class="card card--back" aria-label="Business card back">
  <div class="wordmark"><span>Barrow Advisory</span><span class="wordmark__dot"></span></div>
  <div class="card__rule"></div>
  <p class="card__web">www.<em>barrowadvisory-example</em>.com</p>
</section>

</body>
</html>
```